Medical Implant company needs a Top Quality Premium Brochure

We need to create a top quality brochure for VIP clients, formed by top spine surgeons. The main goal here is to cause a deep quality impact, positioning the company and it´s solutions above the others, with a refined, unique and creative material.

Special paper, hot stamping, innovative format are welcome.

For more information check out our website: www.corvalento.com.br (web translator are recommended for content understanding)

Corvalento works with top quality spine and pain management products, providing solutions for the medical specialists, investing in high quality processes and continued medical education.

Short briefing:
1 - Company profile
2 - Quality / vision
3 - Continued education programs
4 - Main products
5 - Main partners
6 - Final stuff (creative final thoughts / considerations)

FORMAT: 25 x 18,5 cm (horizontal)
PAGES - 16

REFERENCES:

https://www.folioquarry.net/gallery/52930184/Medical-Healthcare-Profile-Brochure

https://www.folioquarry.net/gallery/7719046/TK-Alpine-Style-Brochure

Target Market(s)

Mainly brazilian spine and neuro surgeons with minimally invasive surgery skills.

Industry/Entity Type

Education

Requirements
Must have

• 18 pages design

1. Cover
2. IMAGE + TITLE - About Us
3. IMAGE + TEXT - About Us
4. IMAGE + TITLE - Vision
5. IMAGE + TEXT - Vision
6. IMAGE + TITLE - Quality
7. IMAGE + TEXT - Quality
8. Timeline Left
9. Timeline Right
10. IMAGE + TITLE - Medical Education
11. IMAGE + TEXT - Medical Education
12. IMAGE + TITLE - Minimally Invasive Technology
13. IMAGE + TEXT - Minimally Invasive Technology
14. IMAGE + TITLE - Impact Phrase
15. IMAGE + TEXT - Impact Phrase
16. Back

As longs as the text is under development and will be placed internally in the winning design, please use 'lorem ipsum' for text areas. The titles can follow the index above.

Nice to have
• The use of office pictures with some style / artistic finish in pages "about us"

```html
<!DOCTYPE html>
<html lang="en">
<head>
<meta charset="utf-8">
<title>Editorial Spread – Welcomewords from the Editor</title>
<link rel="stylesheet" href="https://fonts.googleapis.com/css2?family=Exo+2:wght@300;600&family=Open+Sans:wght@400;600&display=swap">
<style>
  :root {
    --brand-green: #1ba34f;
    --brand-green-dark: #158a41;
    --page-white: #ffffff;
    --backdrop: #e9eaeb;
    --text-grey: #4a4a4a;
    --photo-light: #e4e1dc;
    --photo-mid: #b9b3aa;
    --photo-dark: #6f6a64;
  }
  * { box-sizing: border-box; margin: 0; padding: 0; }
  html, body {
    width: 1200px; height: 900px; overflow: hidden;
    background: var(--backdrop);
  }
  .spread {
    position: absolute; left: 40px; top: 243px;
    width: 1120px; height: 414px;
    display: flex;
    box-shadow: 0 6px 24px rgba(0,0,0,.18);
  }
  .page { position: relative; width: 560px; height: 414px; overflow: hidden; }

  /* Left page: office photo mosaic */
  .page--gallery { background: var(--brand-green); }
  .gallery { position: absolute; inset: 0; transform: rotate(-3deg); }
  .gallery__tile {
    position: absolute;
    border: 5px solid var(--page-white);
    background: linear-gradient(160deg, var(--photo-light) 0%, var(--photo-mid) 60%, var(--photo-dark) 100%);
  }
  .tile-1 { left: 120px; top: 40px;  width: 215px; height: 118px; }
  .tile-2 { left: 350px; top: 62px;  width: 150px; height: 96px; }
  .tile-3 { left: 40px;  top: 172px; width: 125px; height: 100px; }
  .tile-4 { left: 178px; top: 172px; width: 160px; height: 130px; }
  .tile-5 { left: 350px; top: 170px; width: 165px; height: 140px; }
  .tile-6 { left: 250px; top: 314px; width: 110px; height: 78px; }

  /* Right page: editorial */
  .page--editorial { background: var(--page-white); }
  .editor-portrait {
    position: absolute; left: 30px; top: 80px; width: 150px; height: 160px;
    background: radial-gradient(ellipse at 55% 55%, #d9dde2 0%, #eef0f2 55%, var(--page-white) 80%);
  }
  .editorial-title {
    position: absolute; left: 195px; top: 92px;
    font: 300 22px/1 "Exo 2", sans-serif;
    color: var(--brand-green);
    white-space: nowrap;
  }
  .editorial-body {
    position: absolute; left: 195px; top: 124px; width: 270px;
    font: 400 9.5px/1.55 "Open Sans", sans-serif;
    color: var(--text-grey);
  }
  .section-tab {
    position: absolute; right: 0; top: 196px; width: 80px; height: 20px;
    background: var(--brand-green);
    color: var(--page-white);
    font: 600 7.5px/20px "Open Sans", sans-serif;
    letter-spacing: 1.2px; text-transform: uppercase;
    text-align: right; padding-right: 10px;
  }
  .page-number {
    position: absolute; right: 40px; bottom: 22px;
    width: 18px; height: 18px; background: var(--brand-green);
    color: var(--page-white);
    font: 600 9px/18px "Open Sans", sans-serif; text-align: center;
  }
</style>
</head>
<body>
  <main class="spread">
    <section class="page page--gallery">
      <div class="gallery">
        <div class="gallery__tile tile-1" role="img" aria-label="Office interior with desks and black chairs"></div>
        <div class="gallery__tile tile-2" role="img" aria-label="Open office workspace with computers"></div>
        <div class="gallery__tile tile-3" role="img" aria-label="Meeting room with a display screen"></div>
        <div class="gallery__tile tile-4" role="img" aria-label="Long workstation row with office chairs"></div>
        <div class="gallery__tile tile-5" role="img" aria-label="Office corner with framed pictures on the wall"></div>
        <div class="gallery__tile tile-6" role="img" aria-label="Reception area with a small round table"></div>
      </div>
    </section>

    <section class="page page--editorial">
      <div class="editor-portrait" role="img" aria-label="Portrait of the editor, a doctor in a white coat with arms crossed"></div>
      <h1 class="editorial-title">Welcomewords from the Editor</h1>
      <p class="editorial-body">Donec sed odio dui. Duis mollis, est non commodo luctus, nisi erat porttitor ligula, eget lacinia odio sem nec elit. Sed posuere consectetur est at lobortis. Nulla vitae elit libero, a pharetra augue. Donec ullamcorper nulla non metus auctor fringilla. Donec id elit non mi porta gravida at eget metus. Fusce dapibus, tellus ac cursus commodo, tortor mauris condimentum nibh, ut fermentum massa justo sit amet risus. Lorem ipsum dolor sit amet, consectetur adipiscing elit. Euismod aenean eu leo quam eget lacinia odio sem nec elit. Sed posuere consectetur est at lobortis. Nulla vitae elit libero, a pharetra augue.</p>
      <div class="section-tab">Editorial</div>
      <div class="page-number">3</div>
    </section>
  </main>
</body>
</html>
```